Designing a brochures for an educational counseling service provider

We would like a 4 sided design on a 11x8.5 paper, half folded. I have including a sample design we did to give you an idea of what we envision but we welcome creativity to make beautiful looking flyers. Text for the flier is included as well as our logo.
- The most important thing is capturing our audience/market. We will be handing these flies to schools, organizations and individual clients.

www.pvrlearningadvisors.example

Target Market(s)

We are targeting international students wanting to study in the U.S and Canada.

Industry/Entity Type

Education

Requirements
Must have
• - Clean and clear
• - Our logo should visible and well placed.
• - Could you the pictures of students, libraries and school buildings or you could use the pictures we already have.
Nice to have
• We would like this to match business cards.

```html
<!DOCTYPE html>
<html lang="en">
<head>
<meta charset="utf-8">
<title>PVR Learning Advisors – Brochure Spread</title>
<link href="https://fonts.googleapis.com/css2?family=Ubuntu:wght@500;700&family=Open+Sans:ital,wght@0,400;0,600;0,700;1,400&display=swap" rel="stylesheet">
<style>
  :root{
    --bg:#ece7e1;
    --paper:#ffffff;
    --green-dark:#2f9e44;
    --green-light:#8cc63f;
    --navy:#1f2a7a;
    --blue:#1e63b0;
    --ink:#2b2b2b;
    --grey-soft:#dcdcdc;
    --photo-warm:#8a6a55;
    --photo-library:#9b8a70;
    --photo-students:#a89a7e;
  }
  *{box-sizing:border-box;margin:0;padding:0}
  html,body{width:1200px;height:900px;overflow:hidden;background:var(--bg)}
  body{font-family:"Open Sans",Arial,sans-serif;color:var(--ink)}
  .spread{position:absolute;left:50px;top:25px;width:1100px;height:850px;display:flex;box-shadow:0 8px 30px rgba(0,0,0,.18)}
  .page{position:relative;width:550px;height:850px;background:var(--paper);overflow:hidden}
  .page--left{background:linear-gradient(180deg,#fff 0%,#fff 38%,#e6e6e6 60%,#fff 100%)}
  .page--right{background:linear-gradient(90deg,#e9e9e9 0%,#fff 30%,#fff 100%)}

  .tab{position:absolute;height:44px;padding:0 22px;display:flex;align-items:center;justify-content:center;
       font-family:"Ubuntu",Arial,sans-serif;font-weight:700;font-size:19px;color:#fff;
       background:linear-gradient(90deg,var(--green-dark),var(--green-light))}
  .photo{position:absolute}

  /* Left page */
  .about-tab{left:110px;top:28px;width:170px}
  .about-photo{left:290px;top:0;width:260px;height:125px;background:linear-gradient(135deg,#5a4336,var(--photo-warm) 55%,#c9a98a)}
  .about-text{position:absolute;left:32px;top:92px;width:250px;font-size:9.6px;line-height:1.4;color:#444}
  .about-text p{margin-bottom:8px}
  .about-text--wide{top:186px;left:32px;width:470px}
  .brand{position:absolute;right:40px;top:312px;display:flex;align-items:center;gap:8px;
         font-family:"Open Sans",Arial,sans-serif;font-weight:700;font-size:13px;color:#fff}
  .brand-dot{width:14px;height:14px;border-radius:50%;background:#fff}
  .library-photo{left:0;top:330px;width:440px;height:480px;background:linear-gradient(160deg,#6b5640,var(--photo-library) 45%,#c7b8a0 70%,#7c6a58)}
  .quote{position:absolute;left:60px;top:690px;width:330px;font-weight:700;font-size:14px;line-height:1.35;color:#fff;
         text-shadow:0 1px 3px rgba(0,0,0,.45)}
  .quote::before{content:"\201C\2009";font-size:20px}
  .quote::after{content:"\2009\201D";font-size:20px}
  .footer-band{position:absolute;left:0;bottom:0;width:550px;height:60px}

  /* Right page */
  .services-tab{left:14px;top:26px;width:150px}
  .services-photo{left:172px;top:0;width:378px;height:140px;background:linear-gradient(120deg,#7c8f55,var(--photo-students) 45%,#c2b49c 70%,#6e7c4b)}
  .intro-band{position:absolute;left:0;top:140px;width:550px;height:50px;background:linear-gradient(90deg,var(--navy),var(--blue));
              color:#fff;font-style:italic;font-size:10px;line-height:1.35;padding:9px 20px 0 40px}
  .content{position:absolute;left:30px;top:198px;width:490px;font-size:9.6px;line-height:1.38;color:#333}
  .package-title{font-family:"Ubuntu",Arial,sans-serif;font-weight:700;font-size:14px;color:var(--green-dark);margin-bottom:3px}
  .package-list{list-style:none;margin-bottom:10px}
  .package-list li{position:relative;padding-left:14px}
  .package-list li::before{content:"";position:absolute;left:0;top:3px;border-left:8px solid var(--navy);border-top:4px solid transparent;border-bottom:4px solid transparent}
  .section-head{display:inline-block;height:26px;line-height:26px;padding:0 30px 0 10px;margin:6px 0 4px;
                font-family:"Ubuntu",Arial,sans-serif;font-weight:700;font-size:14px;color:#fff;
                background:linear-gradient(90deg,var(--green-dark),var(--green-light));
                clip-path:polygon(0 0,calc(100% - 14px) 0,100% 50%,calc(100% - 14px) 100%,0 100%)}
  .content p{margin-bottom:6px}
</style>
</head>
<body>
<main class="spread">
  <section class="page page--left">
    <div class="tab about-tab">About Us</div>
    <div class="photo about-photo" role="img" aria-label="Photo of smiling students studying together"></div>
    <div class="about-text">
      <p>Our mission is to make quality education accessible and affordable to the families we serve. Our services are designed with the child's future in mind.</p>
    </div>
    <div class="about-text about-text--wide">
      <p>Whether one is seeking an academic or non-academic environment, it is important to us that we set our clients up for success.</p>
      <p>We are a family-centered organization and our goals are the same as those of our clients: for their child to thrive and reach their goals and dreams. With over 10 years of experience in the business, we are aware of the financial obstacles created by the ever increasing cost in education. Our expert consultants work closely with families to map out their educational budget and find the best affordable and quality educational options.</p>
    </div>
    <div class="brand"><span class="brand-dot"></span>PVR Learning Advisors</div>
    <div class="photo library-photo" role="img" aria-label="Photo of a student reaching for a book on library shelves"></div>
    <p class="quote">We offer comprehensive services to families, students, institutions and governmental organizations.</p>
    <svg class="footer-band" viewBox="0 0 550 60" preserveAspectRatio="none" aria-hidden="true">
      <path d="M0 20 Q275 48 550 30 L550 60 L0 60 Z" fill="var(--navy)"/>
      <path d="M0 14 Q275 42 550 24 L550 30 Q275 48 0 20 Z" fill="var(--blue)"/>
    </svg>
  </section>

  <section class="page page--right">
    <div class="tab services-tab">Services</div>
    <div class="photo services-photo" role="img" aria-label="Photo of a group of smiling students outdoors"></div>
    <div class="intro-band">Finding the right school or program for your child is one of the most important decisions your family will make. The right choice will make a major impact on your child's future.</div>
    <div class="content">
      <h2 class="package-title">Our package includes</h2>
      <ul class="package-list">
        <li>Intake interview</li>
        <li>Present range of options based on needs and goals of the family</li>
        <li>Interview coaching</li>
        <li>Assistance with application and essays</li>
        <li>Updates on student progress throughout their enrollment with the school</li>
        <li>Advisement on financial documents and visa applications</li>
      </ul>
      <h3 class="section-head">Boarding schools</h3>
      <p>Students who want the best out of their grade school experience are likely to choose boarding schools because they are proven to better prepare students for university. North American boarding schools provide a quality dynamic experience that will facilitate personal growth in independence, leadership and confidence as well as provide the academic curriculum necessary to prepare students for university.</p>
      <h3 class="section-head">College admission</h3>
      <p>As Educational Consultants, we specialize in college/university admissions and we understand how confusing, time-consuming, and stressful the application process can be. Our experienced counselors are here to answer your questions and guide you step by step. As parents and students may have limited access to information on schools, may not know or understand the entire process as a whole, nor know where to begin, our experts counselors have a solution.</p>
      <p>Clients increase the odds of admission with our comprehensive plan of action. We believe that regardless of a student's level of involvement in extracurricular activities or preparedness, they still possess something they can offer to the university. We show we help them shine on their college applications.</p>
      <h3 class="section-head">Transfer students</h3>
      <p>Need to find a school or alternative school that is a better match for you? We work with students and families to transfer from one school to another.</p>
      <h3 class="section-head">Boarding schools</h3>
      <p>Funding the education for your children in some of the world's top schools can be very expensive as tuition and fees increase at an average of 4% every year. We work with you to determine the budget for your family, applying to scholarships available and guide you through the financial aid process.</p>
      <p>Over 70% of our clients have been awarded scholarships or financial aid, making your education goals attainable and affordable for your children's education possible.</p>
      <p>Our consultants are members of NAEC, the leading association for educational consultants in North America.</p>
    </div>
    <svg class="footer-band" viewBox="0 0 550 60" preserveAspectRatio="none" aria-hidden="true">
      <path d="M0 30 Q275 48 550 20 L550 60 L0 60 Z" fill="var(--navy)"/>
      <path d="M0 24 Q275 42 550 14 L550 20 Q275 48 0 30 Z" fill="var(--blue)"/>
    </svg>
  </section>
</main>
</body>
</html>
```